Website design needed for gift based dropship website

I am building a dropshipping website that will create gift based merchandise and send it out to our clients customers for them. Our clients will sell products and when a customer buys from them, we create the item and send it out to the customer.

I am looking for a very similar website to stitchora.com - that website is doing a very similar thing to what i am doing but where the stitchora website is based around clothing, my website will be based around gifts. Another website that i like that is doing a similar thing to what i will do is pelvane.com

I require 2 pages to be made:
1) The home page
2) A landing page for a free product giveaway offer

1) THE HOME PAGE
The home page should be a merger of the two previously stated websites (www.pelvane.com and www.stitchora.com). The style fo the homepage should be based on the logo that is attached and the colour scheme should be similar but basic.

2) THE LANDING PAGE
The landing page will be giving away a free mobile phone cover. The page needs to have some mobile phone covers for different phones all with random designs on. The page should state that they can have any design that they want and they do not pay for the phone (they only pay for shipping).

Menu pages and text should be taken from the stitchora.com website.

Target Market(s)

18 - 40 year old males. People who like the idea of earning extra money in their spare time but aren't too sure how to do it. Semi-professional jobs.

Font styles to use
Serif
Sans Serif
Decorative
Script

Colors

Designer to choose colors to be used in the design.

Requirements
Must have
• A "how it works" image where the dropshipping process is explained to a visitor to the website (similar to the one on the stitchora "how it works page")
Nice to have
• Testimonial area on homepage
Should not have
• Homepage should not have:
• - "latest orders from" area
• - Video
• - Warehousing/fulfilment area
• - Integration area

```html
<!DOCTYPE html>
<html lang="en">
<head>
<meta charset="utf-8">
<title>Parcelwise – Sell Gift Online</title>
<link rel="stylesheet" href="https://fonts.googleapis.com/css2?family=Oswald:wght@500;700&family=Open+Sans:wght@400;600;700&display=swap">
<style>
:root{
  --red:#e8382b;
  --maroon:#5b1522;
  --ink:#2a2a2a;
  --muted:#7a7a7a;
  --line:#e3e3e3;
  --soft:#f5f5f5;
  --tile-grey:#d2c8c6;
  --stage:#e9e9ea;
  --white:#ffffff;
  --star:#f3b81f;
}
*{box-sizing:border-box;margin:0;padding:0}
html,body{width:1200px;height:3315px;overflow:hidden}
body{background:var(--stage);font-family:"Open Sans",Arial,sans-serif;color:var(--ink);position:relative}
.page{position:absolute;background:var(--white);overflow:hidden;box-shadow:0 2px 14px rgba(0,0,0,.12)}
.desk{left:49px;top:33px;width:775px;height:1949px}
.mob{left:880px;top:122px;width:265px;height:3034px}
.heading{font-family:"Oswald",Arial,sans-serif;font-weight:500;text-transform:uppercase;text-align:center;color:var(--ink);white-space:nowrap}
.heading em{font-style:normal;color:var(--red)}
.photo{display:block}
.btn-red{display:inline-block;background:var(--red);color:var(--white);font-weight:700;text-transform:uppercase;white-space:nowrap}
.step{display:flex;justify-content:space-between;align-items:center;background:var(--maroon);color:var(--white);font-weight:700;text-transform:uppercase;white-space:nowrap}
.stars{color:var(--star);letter-spacing:1px}
.stars span{color:#cfcfcf}
.copy{background:var(--maroon);color:var(--white);display:flex;align-items:center}
.social{display:flex;gap:6px}
.social i{display:block;width:9px;height:9px;border-radius:50%;background:var(--white)}
.brand{font-family:"Oswald",Arial,sans-serif;font-weight:700;color:var(--maroon);text-transform:uppercase;display:flex;align-items:center;white-space:nowrap}
.brand b{display:block;background:var(--red);border-radius:50%;margin-right:6px}
.arrow{position:absolute;border-radius:50%;display:flex;align-items:center;justify-content:center}
.arrow.prev{background:#f2b5b0}
.arrow.next{background:var(--ink)}

/* ---------- desktop ---------- */
.desk .topbar{height:20px;display:flex;justify-content:space-between;align-items:center;padding:0 100px;font-size:6px;font-weight:600;border-bottom:1px solid var(--line)}
.desk .header{height:35px;display:flex;justify-content:space-between;align-items:center;padding:0 100px}
.desk .phone{display:flex;align-items:center;gap:5px;font-size:7px;font-weight:700}
.desk .brand{font-size:13px;line-height:1}
.desk .brand b{width:16px;height:16px}
.desk .search{width:84px;height:14px;border:1px solid var(--line)}
.desk .nav{height:22px;display:flex;align-items:center;padding:0 100px;gap:30px;font-size:6px;font-weight:600;text-transform:uppercase;border-bottom:1px solid var(--line);white-space:nowrap}
.desk .nav .active{color:var(--red);border-bottom:1px solid var(--red);padding-bottom:4px;margin-top:5px}
.desk .nav .basket{margin-left:auto;color:var(--red)}
.desk .hero{height:347px;position:relative;background:radial-gradient(ellipse at 50% 45%,#f4efee 0%,#f1e1df 45%,#e9c5c2 100%);text-align:center;padding-top:165px}
.desk .hero h1{font-family:"Oswald",Arial,sans-serif;font-weight:700;font-size:38px;line-height:1;color:var(--ink)}
.desk .hero p{font-size:8px;font-weight:700;width:150px;margin:8px auto 10px;line-height:1.3}
.desk .hero .ghost{display:inline-block;background:var(--white);border:1px solid #cfcfcf;font-size:7px;font-weight:700;padding:6px 10px}
.desk .products{height:365px;background:var(--soft);position:relative;padding-top:48px}
.desk .heading{font-size:15px}
.desk .cards{display:flex;justify-content:center;gap:11px;margin-top:20px}
.desk .card{width:155px;text-align:center}
.desk .card .photo{width:155px;height:175px}
.desk .card h3{font-size:7.5px;font-weight:600;margin-top:8px;white-space:nowrap}
.desk .card h3 strong{font-weight:700}
.desk .card p{font-size:5.5px;color:var(--muted);margin:3px 0 7px}
.desk .card .btn-red{font-size:5.5px;padding:3px 8px}
.desk .arrow{width:14px;height:14px;top:248px}
.desk .products .prev{left:124px}
.desk .products .next{left:643px}
.desk .how{height:416px;padding-top:45px}
.desk .how .frame{width:510px;height:330px;margin:0 auto;border:4px solid #efefef;padding-top:18px}
.desk .how .heading{font-size:14px}
.desk .steps{display:flex;justify-content:center;gap:17px;margin-top:14px}
.desk .col{width:150px;text-align:center}
.desk .tile{position:relative;display:flex;align-items:center;justify-content:center}
.desk .num{position:absolute;top:0;right:0;width:28px;height:28px;background:var(--white);font-family:"Oswald",Arial,sans-serif;font-weight:700;font-size:13px;display:flex;align-items:center;justify-content:center}
.desk .t1{width:152px;height:148px;background:var(--red)}
.desk .t2{width:150px;height:243px;background:var(--tile-grey);flex-direction:column;justify-content:flex-start;padding-top:95px}
.desk .t3{width:130px;height:117px;background:var(--tile-grey)}
.desk .t4{width:130px;height:117px;background:var(--maroon);margin-top:9px}
.desk .col h4{font-size:7.5px;font-weight:700;margin-top:14px}
.desk .col small{display:block;font-size:5.5px;color:var(--muted);width:90px;margin:6px auto 8px;line-height:1.5}
.desk .step{width:65px;height:10px;font-size:5px;padding:0 5px;margin:0 auto}
.desk .t2 small{display:block;font-size:5.5px;color:var(--ink);width:80px;line-height:1.5;margin-top:30px}
.desk .t2 h5{font-size:7.5px;font-weight:700;margin:6px 0 8px}
.desk .inner{position:absolute;left:8px;bottom:8px;text-align:left}
.desk .inner span{display:block;font-size:5.5px}
.desk .inner h5{font-size:7px;font-weight:700;margin:3px 0 5px}
.desk .inner .step{margin:0}
.desk .t4 .inner{color:var(--white)}
.desk .t3 svg,.desk .t4 svg{position:absolute;left:10px;top:10px}
.desk .reviews{height:335px;position:relative;border-top:1px solid var(--line);padding-top:32px}
.desk .reviews .sub{text-align:center;font-size:5.5px;color:var(--muted);margin-top:2px}
.desk .review{width:155px;text-align:center}
.desk .review .photo{width:155px;height:150px}
.desk .review .stars{font-size:7px;margin-top:5px}
.desk .review p{font-size:5.5px;font-weight:600;text-transform:uppercase;width:120px;margin:3px auto 6px;line-height:1.4}
.desk .review .btn-red{font-size:5px;padding:2px 8px}
.desk .reviews .arrow{top:188px}
.desk .reviews .prev{left:124px}
.desk .reviews .next{left:643px}
.desk .signup{height:151px;border-top:1px solid var(--line);display:flex;align-items:center;justify-content:center}
.desk .signup .box{width:520px;height:70px;border:4px solid #efefef;display:flex;align-items:center;gap:14px;padding:0 18px}
.desk .signup h2{font-family:"Oswald",Arial,sans-serif;font-weight:700;color:var(--red);font-size:13px;line-height:1.05;text-transform:uppercase;width:125px}
.desk .field{width:135px;height:20px;border:1px solid var(--line);font-size:6px;color:#aaa;padding:6px}
.desk .signup .btn-red{font-size:7px;padding:7px 14px}
.desk .footer{height:172px;border-top:1px solid var(--line);display:flex;padding:20px 100px 0;gap:30px}
.desk .footer .about{width:270px}
.desk .footer .about p{font-size:5.5px;color:var(--muted);line-height:1.55;margin-top:6px}
.desk .footer h6{font-size:7px;font-weight:700;margin-bottom:6px}
.desk .footer ul{list-style:none;font-size:5.5px;color:var(--muted);line-height:1.75;white-space:nowrap}
.desk .footer .pair{display:flex;gap:30px}
.desk .bottomtext{height:60px;border-top:1px solid var(--line);font-size:5.5px;color:var(--muted);text-align:center;line-height:1.6;padding:8px 150px 0}
.desk .copy{height:26px;justify-content:space-between;padding:0 100px 0 50px;font-size:5.5px}

/* ---------- mobile ---------- */
.mob .topbar{height:17px;display:flex;justify-content:space-between;align-items:center;padding:0 8px;font-size:5px;font-weight:600}
.mob .header{height:75px;display:flex;justify-content:space-between;align-items:center;padding:0 12px 16px;border-bottom:1px solid var(--line)}
.mob .phone{display:flex;align-items:center;gap:3px;font-size:6px;font-weight:700;white-space:nowrap}
.mob .brand{font-size:10px;line-height:1}
.mob .brand b{width:12px;height:12px;margin-right:4px}
.mob .hero{height:400px;background:radial-gradient(ellipse at 50% 40%,#f4efee 0%,#f0dfdd 50%,#e6c2bf 100%);text-align:center;padding-top:170px}
.mob .hero h1{font-family:"Oswald",Arial,sans-serif;font-weight:700;font-size:30px;line-height:1;white-space:nowrap}
.mob .hero p{font-size:7px;font-weight:700;width:150px;margin:8px auto 8px;line-height:1.3}
.mob .hero .ghost{display:inline-block;background:var(--white);border:1px solid #cfcfcf;font-size:6px;font-weight:700;padding:5px 8px}
.mob .products{height:358px;background:var(--soft);position:relative;padding-top:28px;text-align:center}
.mob .heading{font-size:14px}
.mob .products .photo{width:165px;height:190px;margin:16px auto 0}
.mob .products h3{font-size:7px;font-weight:600;margin-top:10px;white-space:nowrap}
.mob .products h3 strong{font-weight:700}
.mob .products p{font-size:5.5px;color:var(--muted);margin:3px 0 7px}
.mob .products .btn-red{font-size:5.5px;padding:3px 8px}
.mob .arrow{width:12px;height:12px}
.mob .products .arrow{top:132px}
.mob .prev{left:8px}
.mob .next{right:8px}
.mob .how{height:950px;padding:30px 12px 0}
.mob .how .frame{height:905px;border:4px solid #efefef;padding-top:22px}
.mob .step{width:75px;height:11px;font-size:5px;padding:0 6px;margin:0 auto}
.mob .stack{display:flex;flex-direction:column;align-items:center;margin-top:18px;text-align:center}
.mob .tile{position:relative;display:flex;align-items:center;justify-content:center}
.mob .num{position:absolute;top:0;right:0;width:26px;height:26px;background:var(--white);font-family:"Oswald",Arial,sans-serif;font-weight:700;font-size:12px;display:flex;align-items:center;justify-content:center}
.mob .t1{width:161px;height:159px;background:var(--red)}
.mob .stack h4{font-size:7px;font-weight:700;margin-top:12px}
.mob .stack > small{display:block;font-size:5.5px;color:var(--muted);width:90px;margin:6px auto 8px;line-height:1.5}
.mob .t2{width:157px;height:261px;background:var(--tile-grey);flex-direction:column;justify-content:flex-start;padding-top:105px;margin-top:34px}
.mob .t2 small{display:block;font-size:5.5px;width:80px;line-height:1.5;margin-top:30px}
.mob .t2 h5{font-size:7px;font-weight:700;margin:6px 0 10px}
.mob .t3{width:144px;height:126px;background:var(--tile-grey);margin-top:16px}
.mob .t4{width:144px;height:122px;background:var(--maroon);margin-top:10px}
.mob .inner{position:absolute;left:8px;bottom:8px;text-align:left}
.mob .inner span{display:block;font-size:5.5px}
.mob .inner h5{font-size:7px;font-weight:700;margin:3px 0 5px}
.mob .inner .step{margin:0}
.mob .t4 .inner{color:var(--white)}
.mob .t3 svg,.mob .t4 svg{position:absolute;left:10px;top:10px}
.mob .reviews{height:387px;position:relative;border-top:1px solid var(--line);padding-top:30px;text-align:center}
.mob .reviews .sub{font-size:5.5px;color:var(--muted);margin-top:2px;white-space:nowrap}
.mob .reviews .photo{width:165px;height:160px;margin:12px auto 0}
.mob .reviews .stars{font-size:7px;margin-top:5px}
.mob .reviews p{font-size:5.5px;font-weight:600;text-transform:uppercase;width:120px;margin:3px auto 8px;line-height:1.4}
.mob .reviews .btn-red{font-size:5px;padding:2px 9px}
.mob .reviews .arrow{top:150px}
.mob .signup{height:254px;border-top:1px solid var(--line);padding:20px 30px 0;text-align:center}
.mob .signup h2{font-family:"Oswald",Arial,sans-serif;font-weight:700;color:var(--red);font-size:14px;line-height:1.1;text-transform:uppercase}
.mob .field{height:20px;border:1px solid var(--line);font-size:5.5px;color:#aaa;padding:6px;text-align:left;margin-top:10px}
.mob .signup .btn-red{font-size:6px;padding:7px 14px;margin-top:18px}
.mob .footer{height:409px;border-top:1px solid var(--line);padding:18px 12px 0}
.mob .footer p{font-size:5.5px;color:var(--muted);line-height:1.55;margin:6px 0 10px}
.mob .footer h6{font-size:7px;font-weight:700;margin:8px 0 6px}
.mob .footer ul{list-style:none;font-size:5.5px;color:var(--muted);line-height:1.8;white-space:nowrap}
.mob .footer .pair{display:flex;gap:60px}
.mob .bottomtext{height:148px;border-top:1px solid var(--line);font-size:5.5px;color:var(--muted);text-align:center;line-height:1.6;padding:14px 20px 0}
.mob .copy{height:36px;flex-direction:column;justify-content:center;gap:6px;font-size:5px}
</style>
</head>
<body>

<!-- Desktop home page -->
<main class="page desk">
  <div class="topbar">
    <span>Free Shipping on $50+ Order</span>
    <span>
      <svg width="6" height="7" viewBox="0 0 6 8"><path d="M3 0a3 3 0 0 1 3 3c0 2-3 5-3 5S0 5 0 3a3 3 0 0 1 3-3z" fill="#2a2a2a"/></svg>
      Shop near you
    </span>
  </div>
  <header class="header">
    <div class="phone">
      <svg width="9" height="9" viewBox="0 0 10 10"><path d="M2 0l2 2-1 2c1 1 2 2 3 3l2-1 2 2-2 2C4 10 0 6 0 2z" fill="#e8382b"/></svg>
      012 345 67890
    </div>
    <div class="brand"><b></b>Parcelwise</div>
    <div class="search"></div>
  </header>
  <nav class="nav">
    <span class="active">Pricing</span><span>How It Works</span><span>Resources</span><span>Mock Up Generator</span><span>FAQ</span><span>Blogs</span><span>Contact Us</span>
    <span class="basket">My Basket</span>
  </nav>

  <section class="hero photo" role="img" aria-label="Smiling woman in a knit hat holding a wrapped present, with red gift boxes floating around her">
    <h1>SELL GIFT ONLINE</h1>
    <p>If you want to sell your designs to an online store or marketplace</p>
    <span class="ghost">Connect Your Shop</span>
  </section>

  <section class="products">
    <h2 class="heading">Our <em>Products</em></h2>
    <div class="cards">
      <div class="card">
        <div class="photo" role="img" aria-label="Pile of colourful wrapped gift boxes with ribbons" style="background:linear-gradient(160deg,#e9e6e6,#c7423c 55%,#3b5fa8)"></div>
        <h3>Lorem Ipsum Dolor <strong>Sit Amet Consect</strong></h3>
        <p>Lorem Ipsum Dolor Sit Amet Consectetur</p>
        <span class="btn-red">From $20.00</span>
      </div>
      <div class="card">
        <div class="photo" role="img" aria-label="Hands holding a gift box wrapped in orange paper on a teal table" style="background:linear-gradient(160deg,#5fc0b8,#e58b43 55%,#5fc0b8)"></div>
        <h3>Lorem Ipsum Dolor <strong>Sit Amet Consect</strong></h3>
        <p>Lorem Ipsum Dolor Sit Amet Consectetur</p>
        <span class="btn-red">From $20.00</span>
      </div>
      <div class="card">
        <div class="photo" role="img" aria-label="Young woman in a festive red sweater holding a gold gift box" style="background:linear-gradient(170deg,#ececec,#e4d6c8 45%,#b52a2e)"></div>
        <h3>Lorem Ipsum Dolor <strong>Sit Amet Consect</strong></h3>
        <p>Lorem Ipsum Dolor Sit Amet Consectetur</p>
        <span class="btn-red">From $20.00</span>
      </div>
    </div>
    <span class="arrow prev"><svg width="6" height="6" viewBox="0 0 6 6"><path d="M4 0L1 3l3 3" stroke="#fff" fill="none"/></svg></span>
    <span class="arrow next"><svg width="6" height="6" viewBox="0 0 6 6"><path d="M2 0l3 3-3 3" stroke="#fff" fill="none"/></svg></span>
  </section>

  <section class="how">
    <div class="frame">
      <h2 class="heading">How <em>It Works</em></h2>
      <div class="steps">
        <div class="col">
          <div class="tile t1">
            <span class="num">1</span>
            <svg width="30" height="30" viewBox="0 0 30 30"><circle cx="15" cy="8" r="5" fill="#fff"/><path d="M7 20c0-4 4-6 8-6s8 2 8 6z" fill="#fff"/><path d="M2 22h8l5 3 13-5v4l-13 6-13-3z" fill="#fff"/></svg>
          </div>
          <h4>Gerry</h4>
          <small>Gerry Buys Something At our Store</small>
          <div class="step"><span>Step - 1</span><span>›</span></div>
        </div>
        <div class="col">
          <div class="tile t2">
            <span class="num">2</span>
            <svg width="28" height="28" viewBox="0 0 28 28"><path d="M2 10l3-7h18l3 7z" fill="#5b1522"/><rect x="4" y="10" width="20" height="15" fill="none" stroke="#5b1522" stroke-width="2"/><rect x="11" y="16" width="6" height="9" fill="#5b1522"/></svg>
            <small>Order Get Sent Automatically To Parcelwise</small>
            <h5>Your Store</h5>
            <div class="step"><span>Step - 2</span><span>›</span></div>
          </div>
        </div>
        <div class="col">
          <div class="tile t3">
            <span class="num">3</span>
            <svg width="26" height="24" viewBox="0 0 26 24"><path d="M2 7l11-5 11 5v12l-11 5-11-5z" fill="#5b1522"/><path d="M2 7l11 5 11-5M13 12v12" stroke="#d2c8c6" stroke-width="1.5" fill="none"/></svg>
            <div class="inner">
              <span>Product Get Made</span>
              <h5>Parcelwise</h5>
              <div class="step"><span>Step - 3</span><span>›</span></div>
            </div>
          </div>
          <div class="tile t4">
            <span class="num">4</span>
            <svg width="30" height="24" viewBox="0 0 30 24"><path d="M1 24V10l8 5V10l8 5V10l8 5V2h4v22z" fill="#fff"/></svg>
            <div class="inner">
              <span>Your Brands All Over It</span>
              <h5>Your Products</h5>
              <div class="step"><span>Step - 4</span><span>›</span></div>
            </div>
          </div>
        </div>
      </div>
    </div>
  </section>

  <section class="reviews">
    <h2 class="heading"><em>What Our Client Says</em></h2>
    <p class="sub">Lorem Ipsum Dolor Sit Amet Consectetur</p>
    <div class="cards">
      <div class="review">
        <div class="photo" role="img" aria-label="Woman in a red holiday sweater hugging a gift box" style="background:linear-gradient(170deg,#ececec,#dccabd 45%,#b3282c)"></div>
        <div class="stars">★★★★<span>★</span></div>
        <p>Lorem ipsum dolor sit amet consectetur dolor sit amet</p>
        <span class="btn-red">More</span>
      </div>
      <div class="review">
        <div class="photo" role="img" aria-label="Blonde woman holding a pink wrapped present against a pink backdrop" style="background:linear-gradient(170deg,#f2a9c6,#e46f9c 55%,#6db5d8)"></div>
        <div class="stars">★★★★<span>★</span></div>
        <p>Lorem ipsum dolor sit amet consectetur dolor sit amet</p>
        <span class="btn-red">More</span>
      </div>
      <div class="review">
        <div class="photo" role="img" aria-label="Dark-haired woman holding a stack of red gift boxes" style="background:linear-gradient(170deg,#f0f0f0,#d9c9c4 45%,#c0262c)"></div>
        <div class="stars">★★★★<span>★</span></div>
        <p>Lorem ipsum dolor sit amet consectetur dolor sit amet</p>
        <span class="btn-red">More</span>
      </div>
    </div>
    <span class="arrow prev"><svg width="6" height="6" viewBox="0 0 6 6"><path d="M4 0L1 3l3 3" stroke="#fff" fill="none"/></svg></span>
    <span class="arrow next"><svg width="6" height="6" viewBox="0 0 6 6"><path d="M2 0l3 3-3 3" stroke="#fff" fill="none"/></svg></span>
  </section>

  <section class="signup">
    <div class="box">
      <h2>Create Your Account For Free</h2>
      <div class="field">Email</div>
      <div class="field">Password</div>
      <span class="btn-red">Sign Up</span>
    </div>
  </section>

  <footer class="footer">
    <div class="about">
      <div class="brand" style="font-size:11px"><b style="width:13px;height:13px"></b>Parcelwise</div>
      <p>Lorem ipsum dolor sit amet, consectetur adipiscing elit, sed do eiusmod tempor incididunt ut labore et dolore magna aliqua. Ut enim ad minim veniam, quis nostrud exercitation ullamco laboris nisi ut aliquip ex ea commodo consequat. Duis aute irure dolor in reprehenderit in voluptate velit esse cillum dolore.</p>
    </div>
    <div>
      <h6>About Us</h6>
      <div class="pair">
        <ul><li>About</li><li>Blog</li><li>Contact</li><li>Careers</li><li>Privacy</li><li>Terms</li></ul>
        <ul><li>How IT Works</li><li>Products</li><li>Contact Us</li><li>Login</li></ul>
      </div>
    </div>
    <div>
      <h6>Parcelwise</h6>
      <ul><li>Pricing</li><li>How it Works</li><li>Resources</li><li>Mock Up Generator</li><li>FAQ</li><li>Blogs</li><li>Contact Us</li></ul>
    </div>
  </footer>
  <div class="bottomtext">Lorem ipsum dolor sit amet, consectetur adipiscing elit, sed do eiusmod tempor incididunt ut labore et dolore magna aliqua. Ut enim ad minim veniam, quis nostrud exercitation ullamco laboris nisi ut aliquip ex ea commodo consequat duis aute irure dolor in reprehenderit voluptate.</div>
  <div class="copy">
    <span>© Copyright 2018 Parcelwise. All Rights Reserved.</span>
    <span class="social"><i></i><i></i><i></i><i></i></span>
  </div>
</main>

<!-- Mobile home page -->
<main class="page mob">
  <div class="topbar">
    <span>Free Shipping on $50+ Order</span>
    <span>Shop near you</span>
  </div>
  <header class="header">
    <div class="phone">
      <svg width="7" height="7" viewBox="0 0 10 10"><path d="M2 0l2 2-1 2c1 1 2 2 3 3l2-1 2 2-2 2C4 10 0 6 0 2z" fill="#e8382b"/></svg>
      012 345 67890
    </div>
    <div class="brand"><b></b>Parcelwise</div>
    <svg width="8" height="8" viewBox="0 0 10 10"><circle cx="4" cy="4" r="3" fill="none" stroke="#7a7a7a" stroke-width="1.4"/><path d="M6.5 6.5L9.5 9.5" stroke="#7a7a7a" stroke-width="1.4"/></svg>
  </header>

  <section class="hero photo" role="img" aria-label="Smiling woman in a knit hat holding a wrapped present, with red gift boxes floating around her">
    <h1>SELL GIFT ONLINE</h1>
    <p>If you want to sell your designs to an online store or marketplace</p>
    <span class="ghost">Connect Your Shop</span>
  </section>

  <section class="products">
    <h2 class="heading">Our <em>Products</em></h2>
    <div class="photo" role="img" aria-label="Pile of colourful wrapped gift boxes with ribbons" style="background:linear-gradient(160deg,#e9e6e6,#c7423c 55%,#3b5fa8)"></div>
    <h3>Lorem Ipsum Dolor <strong>Sit Amet Consect</strong></h3>
    <p>Lorem Ipsum Dolor Sit Amet Consectetur</p>
    <span class="btn-red">From $20.00</span>
    <span class="arrow prev"><svg width="5" height="5" viewBox="0 0 6 6"><path d="M4 0L1 3l3 3" stroke="#fff" fill="none"/></svg></span>
    <span class="arrow next"><svg width="5" height="5" viewBox="0 0 6 6"><path d="M2 0l3 3-3 3" stroke="#fff" fill="none"/></svg></span>
  </section>

  <section class="how">
    <div class="frame">
      <h2 class="heading">How <em>It Works</em></h2>
      <div class="stack">
        <div class="tile t1">
          <span class="num">1</span>
          <svg width="30" height="30" viewBox="0 0 30 30"><circle cx="15" cy="8" r="5" fill="#fff"/><path d="M7 20c0-4 4-6 8-6s8 2 8 6z" fill="#fff"/><path d="M2 22h8l5 3 13-5v4l-13 6-13-3z" fill="#fff"/></svg>
        </div>
        <h4>Gerry</h4>
        <small>Gerry Buys Something At our Store</small>
        <div class="step"><span>Step - 1</span><span>›</span></div>

        <div class="tile t2">
          <span class="num">2</span>
          <svg width="28" height="28" viewBox="0 0 28 28"><path d="M2 10l3-7h18l3 7z" fill="#5b1522"/><rect x="4" y="10" width="20" height="15" fill="none" stroke="#5b1522" stroke-width="2"/><rect x="11" y="16" width="6" height="9" fill="#5b1522"/></svg>
          <small>Order Get Sent Automatically To Parcelwise</small>
          <h5>Your Store</h5>
          <div class="step"><span>Step - 2</span><span>›</span></div>
        </div>

        <div class="tile t3">
          <span class="num">3</span>
          <svg width="26" height="24" viewBox="0 0 26 24"><path d="M2 7l11-5 11 5v12l-11 5-11-5z" fill="#5b1522"/><path d="M2 7l11 5 11-5M13 12v12" stroke="#d2c8c6" stroke-width="1.5" fill="none"/></svg>
          <div class="inner">
            <span>Product Get Made</span>
            <h5>Parcelwise</h5>
            <div class="step"><span>Step - 3</span><span>›</span></div>
          </div>
        </div>

        <div class="tile t4">
          <span class="num">4</span>
          <svg width="30" height="24" viewBox="0 0 30 24"><path d="M1 24V10l8 5V10l8 5V10l8 5V2h4v22z" fill="#fff"/></svg>
          <div class="inner">
            <span>Your Brands All Over It</span>
            <h5>Your Products</h5>
            <div class="step"><span>Step - 4</span><span>›</span></div>
          </div>
        </div>
      </div>
    </div>
  </section>

  <section class="reviews">
    <h2 class="heading"><em>What Our Client Says</em></h2>
    <p class="sub">Lorem Ipsum Dolor Sit Amet Consectetur</p>
    <div class="photo" role="img" aria-label="Woman in a red holiday sweater hugging a gift box" style="background:linear-gradient(170deg,#ececec,#dccabd 45%,#b3282c)"></div>
    <div class="stars">★★★★<span>★</span></div>
    <p>Lorem ipsum dolor sit amet consectetur dolor sit amet</p>
    <span class="btn-red">More</span>
    <span class="arrow prev"><svg width="5" height="5" viewBox="0 0 6 6"><path d="M4 0L1 3l3 3" stroke="#fff" fill="none"/></svg></span>
    <span class="arrow next"><svg width="5" height="5" viewBox="0 0 6 6"><path d="M2 0l3 3-3 3" stroke="#fff" fill="none"/></svg></span>
  </section>

  <section class="signup">
    <h2>Create Your<br>Account For Free</h2>
    <div class="field">Email</div>
    <div class="field">Password</div>
    <span class="btn-red">Sign Up</span>
  </section>

  <footer class="footer">
    <div class="brand" style="font-size:11px"><b style="width:13px;height:13px"></b>Parcelwise</div>
    <p>Lorem ipsum dolor sit amet, consectetur adipiscing elit, sed do eiusmod tempor incididunt ut labore et dolore magna aliqua. Ut enim ad minim veniam, quis nostrud exercitation ullamco laboris nisi ut aliquip ex ea commodo consequat.</p>
    <h6>About Us</h6>
    <div class="pair">
      <ul><li>About</li><li>Blog</li><li>Contact</li><li>Careers</li><li>Privacy</li><li>Terms</li></ul>
      <ul><li>How IT Works</li><li>Products</li><li>Contact Us</li><li>Login</li></ul>
    </div>
    <h6>Parcelwise</h6>
    <ul><li>Pricing</li><li>How it Works</li><li>Resources</li><li>Mock Up Generator</li><li>FAQ</li><li>Blogs</li><li>Contact Us</li></ul>
  </footer>
  <div class="bottomtext">Lorem ipsum dolor sit amet, consectetur adipiscing elit, sed do eiusmod tempor incididunt ut labore et dolore magna aliqua. Ut enim ad minim veniam, quis nostrud exercitation ullamco laboris nisi ut aliquip ex ea commodo consequat duis aute irure dolor in reprehenderit voluptate.</div>
  <div class="copy">
    <span>© Copyright 2018 Parcelwise. All Rights Reserved.</span>
    <span class="social"><i></i><i></i><i></i><i></i></span>
  </div>
</main>

</body>
</html>
```